Bry7Legal Letterhead

Need a new letterhead for my law firm.
IDENTIFYING INFORMATION BELOW:
Anselmo R Quintara III
Attorney at Law
Address: 2847 Larkspur Blvd, Ste 300, Dallas, TX 75204
Phone: 877-482-6017
Fax: 469-738-1452
Email: bry@bry7legal.example
Website: www.bry7legal.example

Colors
0054AA
0677BA
7BADD7
CADEEF
E8F1F8

Requirements
Must have
• Logo needs to be on the letterhead, along with identifying information which is included in the project description.

```html
<!DOCTYPE html>
<html lang="en">
<head>
<meta charset="utf-8">
<title>Bry7Legal Letterhead</title>
<link href="https://fonts.googleapis.com/css2?family=Inter:wght@400;600;800&family=Arimo:wght@400&display=swap" rel="stylesheet">
<style>
  :root {
    --backdrop: #ababab;
    --paper: #ffffff;
    --ink: #111111;
    --body-ink: #4a4a4a;
    --accent: #0a9be0;
    --rule: #0677ba;
    --signature-fill: #e6e8eb;
  }
  * { margin: 0; padding: 0; box-sizing: border-box; }
  html, body { width: 1039px; height: 1200px; overflow: hidden; background: var(--backdrop); }
  .letterhead {
    position: absolute; left: 159px; top: 98px; width: 710px; height: 1001px;
    background: var(--paper); font-family: "Inter", sans-serif; color: var(--ink);
  }
  .brand { position: absolute; left: 58px; top: 80px; width: 188px; text-align: center; }
  .brand-name { font-weight: 800; font-size: 27px; line-height: 28px; letter-spacing: 0.5px; color: var(--ink); }
  .brand-tagline { font-size: 11px; letter-spacing: 2px; margin-top: 2px; color: var(--ink); }
  .attorney { position: absolute; right: 45px; top: 82px; text-align: right; }
  .attorney-name { font-weight: 600; font-size: 18px; line-height: 22px; }
  .attorney-title { font-size: 11px; color: var(--accent); margin-top: 1px; letter-spacing: 0.2px; }
  .edge-tab { position: absolute; right: 0; top: 83px; width: 17px; height: 39px; background: var(--accent); }
  .letter { position: absolute; left: 53px; top: 335px; width: 600px; font-family: "Arimo", sans-serif; color: var(--body-ink); }
  .salutation { font-size: 14.5px; margin-bottom: 15px; }
  .letter p { font-size: 10.8px; line-height: 16.8px; text-align: justify; margin-bottom: 16.8px; }
  .closing { margin-top: 0; }
  .signature { position: absolute; left: 55px; top: 678px; width: 90px; height: 36px; background: var(--signature-fill); border-radius: 3px; }
  .contact-bar { position: absolute; left: 0; top: 920px; width: 100%; height: 30px; font-size: 10.5px; line-height: 13px; }
  .contact-col { position: absolute; top: 3px; }
  .contact-col.address { left: 69px; }
  .contact-col.phones { left: 309px; }
  .contact-col.online { left: 513px; }
  .contact-divider { position: absolute; top: 0; width: 1px; height: 24px; background: var(--rule); }
  .contact-line { display: flex; align-items: center; gap: 5px; }
  .contact-line svg { width: 9px; height: 9px; flex: none; fill: var(--accent); }
</style>
</head>
<body>
  <div class="letterhead">
    <div class="brand">
      <div class="brand-name">Bry7Legal</div>
      <div class="brand-tagline">LAW THAT MOVES</div>
    </div>
    <div class="attorney">
      <div class="attorney-name">Anselmo R Quintara III</div>
      <div class="attorney-title">Attorney at Law</div>
    </div>
    <div class="edge-tab"></div>

    <div class="letter">
      <div class="salutation">Dear Mr. Hallorway,</div>
      <p>Lorem ipsum dolor sit amet, consectetur adipiscing elit. Donec orci purus, luctus vitae dignissim eu, iaculis sed purus. Vivamus faucibus, ipsum nec aliquet viverra, leo mauris condimentum ligula, sit amet sagittis enim ligula quis arcu. Nam egestas tortor id nisi porttitor mattis. In tortor ante, ultricies in suscipit a, tempus non massa. Vivamus et auctor mi. Fusce vel massa nulla. Phasellus nec eros mauris, et scelerisque orci.</p>
      <p>Donec malesuada orci vitae nulla accumsan porta a id massa. Quisque accumsan iaculis magna sit amet fringilla. Maecenas consequat, magna eget tincidunt semper, odio nibh rutrum mi, id feugiat ante nisi eu risus. Vestibulum nunc orci, rhoncus a placerat in, ultricies in mi. Cras mattis varius eros, vel fringilla nisi suscipit eget. Quisque scelerisque sagittis nulla at porttitor.</p>
      <p>Sed id augue vitae urna euismod commodo aliquet a quam. Pellentesque arcu velit, cursus et malesuada ut, consequat et diam. Nullam erat sem, rhoncus id ullamcorper vitae, rhoncus et arcu. In ultricies ultricies nulla, ut rutrum nisi iaculis at. Donec eu magna a metus ornare faucibus. Fusce aliquet faucibus ultricies. Morbi semper, est id tincidunt gravida, sem arcu adipiscing lacus, ac bibendum nulla leo eu purus. Quisque nec diam sed risus consectetur a ccumsan quis quis nibh. Vestibulum id purus lorem.</p>
      <p class="closing">Sincerely,</p>
    </div>
    <div class="signature" role="img" aria-label="Handwritten signature of the attorney"></div>

    <div class="contact-bar">
      <div class="contact-col address">2847 Larkspur Blvd<br>Ste 300, Dallas, TX 75204</div>
      <div class="contact-divider" style="left:255px"></div>
      <div class="contact-col phones">
        <div class="contact-line"><svg viewBox="0 0 10 10" aria-hidden="true"><path d="M2 0.5 L3.6 0.5 L4.3 2.6 L3.2 3.5 Q4 5.6 6.4 6.8 L7.4 5.7 L9.5 6.4 L9.5 8 Q9.5 9.5 8 9.5 Q0.5 8.5 0.5 2 Q0.5 0.5 2 0.5 Z"/></svg>877-482-6017</div>
        <div class="contact-line"><svg viewBox="0 0 10 10" aria-hidden="true"><rect x="2.5" y="0.5" width="5" height="3"/><rect x="0.5" y="3.5" width="9" height="4" rx="1"/><rect x="2.5" y="7" width="5" height="2.5"/></svg>469-738-1452</div>
      </div>
      <div class="contact-divider" style="left:458px"></div>
      <div class="contact-col online">
        <div class="contact-line"><svg viewBox="0 0 10 10" aria-hidden="true"><path d="M0.5 2 H9.5 V8.5 H0.5 Z M1 2.5 L5 5.5 L9 2.5" stroke="#fff" stroke-width="0.6"/></svg>bry@bry7legal.example</div>
        <div class="contact-line"><svg viewBox="0 0 10 10" aria-hidden="true"><circle cx="5" cy="5" r="4.3" fill="none" stroke="#0a9be0" stroke-width="0.8"/><ellipse cx="5" cy="5" rx="1.8" ry="4.3" fill="none" stroke="#0a9be0" stroke-width="0.7"/><path d="M0.8 5 H9.2 M1.5 3 H8.5 M1.5 7 H8.5" stroke="#0a9be0" stroke-width="0.6"/></svg>www.bry7legal.example</div>
      </div>
    </div>
  </div>
</body>
</html>
```